KAJU Freightways #ALLKAJU Business Cards & Letterhead

I am looking to business cards designed for our organization. We are currently undergoing a small re-branding that is taking place. Our organization is called KAJU Freightways and we are headquartered in Phoenix, AZ. We primarily provide transportation and logistics services to the Marlow Parcel Bureau who is our largest customer. I would like to see a design that incorporates name, title, contact info, website, and address (this will be different depending on the employee). I would also like to see some color on the business card using our logo colors or a variation. I would like our logo on the back of the business card with the website displayed. The final design should communicate that we are a next generation transportation operate that focuses on being driver-first, customer-centric, innovative, and sustainable.We would also like our #ALLKAJU catch phrase incorporated as well.

Target Market(s)

Transportation & Logistics

Industry/Entity Type

Trucking Company

Contact Information for Business Card

-First and Last Name
-Position Title
-Contact Phone
-Contact Email
-Physical Address

Font styles to use
Serif

Colors

Designer to choose colors to be used in the design.

Requirements
Must have
• -KAJU logo prominently displayed
• -#ALLKAJU catch phrase used
• -Some amount of color, design gradient, etc.
• -Logo on the back with website listed (https://www.kajufreightco.example)

```html
<!DOCTYPE html>
<html lang="en">
<head>
<meta charset="utf-8">
<title>KAJU Freightways Business Card</title>
<link rel="stylesheet" href="https://fonts.googleapis.com/css2?family=Source+Serif+4:wght@400;600;700&display=swap">
<style>
  :root {
    --page-bg: #c9c9c9;
    --card-white: #ffffff;
    --brand-green: #7dc242;
    --brand-navy: #053744;
    --map-tone: #0c4452;
    --text-dark: #1f4450;
  }
  * { box-sizing: border-box; margin: 0; padding: 0; }
  html, body {
    width: 1125px; height: 1200px; overflow: hidden;
    background: var(--page-bg);
    font-family: "Source Serif 4", Georgia, serif;
  }
  .canvas { position: relative; width: 1125px; height: 1200px; }

  .card {
    position: absolute; left: 150px; width: 826px; height: 472px;
    border-radius: 24px; overflow: hidden;
    box-shadow: 0 3px 6px rgba(0,0,0,.35);
  }
  .card--front { top: 98px; background: var(--card-white); }
  .card--back { top: 631px; background: var(--brand-navy); }

  /* Front */
  .brand-mark {
    position: absolute; left: 160px; top: 196px; width: 230px; height: 74px;
    display: flex; align-items: center; gap: 14px;
  }
  .brand-mark__dot {
    width: 26px; height: 26px; border-radius: 50%; background: var(--brand-green); flex: none;
  }
  .brand-mark__name {
    font-weight: 700; font-size: 60px; line-height: 1; letter-spacing: 1px;
    color: var(--brand-navy);
  }
  .divider {
    position: absolute; left: 413px; top: 124px; width: 1px; height: 222px;
    background: var(--brand-navy); opacity: .8;
  }
  .contact {
    position: absolute; left: 453px; top: 120px; color: var(--text-dark);
  }
  .contact__name {
    font-weight: 600; font-size: 28px; color: var(--brand-green); line-height: 1.1;
  }
  .contact__title { font-size: 20px; margin-top: 4px; line-height: 1.2; }
  .contact__address { font-size: 20px; margin-top: 16px; line-height: 1.3; }
  .contact__list { list-style: none; margin-top: 12px; font-size: 20px; }
  .contact__item { display: flex; align-items: center; gap: 12px; height: 26px; }
  .contact__icon { width: 17px; height: 17px; flex: none; }
  .contact__accent { color: var(--brand-green); }
  .swoosh { position: absolute; left: 0; bottom: 0; width: 826px; height: 472px; }

  /* Back */
  .world-map {
    position: absolute; left: 8px; top: 6px; width: 810px; height: 450px;
    background: radial-gradient(ellipse at 55% 45%, var(--map-tone) 0%, var(--brand-navy) 70%);
    opacity: .9;
  }
  .brand-mark--back {
    left: 0; top: 150px; width: 826px; height: 120px;
    justify-content: center; gap: 22px;
  }
  .brand-mark--back .brand-mark__dot { width: 40px; height: 40px; }
  .brand-mark--back .brand-mark__name { font-size: 108px; color: var(--card-white); }
  .back-footer {
    position: absolute; left: 0; top: 322px; width: 826px;
    text-align: center; color: var(--card-white);
  }
  .back-footer__tag {
    font-weight: 700; font-size: 24px; letter-spacing: 3px; color: var(--brand-green);
  }
  .back-footer__web { font-size: 20px; margin-top: 8px; }
</style>
</head>
<body>
<main class="canvas">
  <section class="card card--front" aria-label="Business card front">
    <div class="brand-mark">
      <span class="brand-mark__dot"></span>
      <span class="brand-mark__name">KAJU</span>
    </div>
    <div class="divider"></div>
    <div class="contact">
      <p class="contact__name">Dana Whitlow</p>
      <p class="contact__title">Manager</p>
      <p class="contact__address">4410 North Canyon Ridge Drive<br>Phoenix, AZ 85021</p>
      <ul class="contact__list">
        <li class="contact__item">
          <svg class="contact__icon" viewBox="0 0 16 16" aria-hidden="true"><path fill="#7dc242" d="M3.5 1.2l2.3 2.6-1.2 1.8c.9 2 2.4 3.6 4.5 4.6l1.8-1.2 2.7 2.2-1.3 2.8C7 13.6 2.4 9 1 3.6z"/></svg>
          <span>602-555-0143</span>
        </li>
        <li class="contact__item">
          <svg class="contact__icon" viewBox="0 0 16 16" aria-hidden="true"><rect x="1" y="3.5" width="14" height="9" fill="#7dc242"/><path d="M1.5 4l6.5 5 6.5-5" fill="none" stroke="#fff" stroke-width="1.2"/></svg>
          <span>info@kajufreightco.example</span>
        </li>
        <li class="contact__item">
          <svg class="contact__icon" viewBox="0 0 16 16" aria-hidden="true"><circle cx="8" cy="8" r="7" fill="#7dc242"/><path d="M1 8h14M8 1c-3 3-3 11 0 14M8 1c3 3 3 11 0 14" fill="none" stroke="#fff" stroke-width="1"/></svg>
          <span>www.<span class="contact__accent">kajufreightco</span>.example</span>
        </li>
      </ul>
    </div>
    <svg class="swoosh" viewBox="0 0 826 472" aria-hidden="true">
      <path fill="#7dc242" d="M0 420 Q320 478 600 458 Q730 446 826 424 L826 472 L0 472 Z"/>
      <path fill="#053744" d="M0 397 Q280 436 565 457 Q290 456 0 418 Z"/>
    </svg>
  </section>

  <section class="card card--back" aria-label="Business card back">
    <div class="world-map" role="img" aria-label="Faint dotted world map in dark teal"></div>
    <div class="brand-mark brand-mark--back">
      <span class="brand-mark__dot"></span>
      <span class="brand-mark__name">KAJU</span>
    </div>
    <div class="back-footer">
      <p class="back-footer__tag">#ALLKAJU</p>
      <p class="back-footer__web">www.kajufreightco.example</p>
    </div>
  </section>
</main>
</body>
</html>
```